Suds Haven Laundromat Wordpress Design

We need a Wordpress website design for our laundromat, Suds Haven Atlanta, at www.sudshavenatlanta-example.com. We would like to have 6 pages: Home, About Us, Services, Locations, Reviews and Contact us. We will provide content for the text on each page. What we do: We are a full service laundromat that provides dry cleaning drop off, professional laundry services, wash dry fold and self service laundry to the local community. We would like to use the color scheme from our logo to convey a warm, safe, and bright business that caters to its diverse community.
Updates

I like the structure of this laundromat website: http://www.washtroveusa-example.com/ Using my logo and color scheme in the above referenced website is what. Am looking for. The photos attached to the project with the female model should be used as a primary focus and supplemented by actual photos of the equipment.

Target Market(s)

Our target market is a diverse group of people from Midtown Atlanta - LGBTQ community /Locals/Regulars that have been coming to laundromat for 30 years.

Industry/Entity Type

Laundromat

Coding

Coded - Design and coding required

Number of Pages Required

5+ page

Font styles to use
Sans Serif

Colors
0054AA
0677BA
7BADD7
CADEEF
E8F1F8

Requirements
Must have
• Feature this video on the main page: https://videohost-example.com/xq7Rm2bPz4k

```html
<!DOCTYPE html>
<html lang="en">
<head>
<meta charset="utf-8">
<title>Suds Haven Atlanta – Home</title>
<link rel="stylesheet" href="https://fonts.googleapis.com/css2?family=Oswald:wght@500;600&family=Arimo:wght@400;700&display=swap">
<style>
:root{
  --blue:#0054AA;
  --blue-mid:#0677BA;
  --cyan:#03A2E0;
  --blue-soft:#7BADD7;
  --blue-pale:#CADEEF;
  --blue-wash:#E8F1F8;
  --ink:#222831;
  --text:#3a3f45;
  --muted:#8a9097;
  --section-grey:#F1F5F9;
  --footer:#2D4A6F;
  --white:#ffffff;
  --star:#F08A24;
}
*{box-sizing:border-box;margin:0;padding:0}
html,body{width:1200px;height:2932px;overflow:hidden}
body{position:relative;font-family:"Arimo",Arial,sans-serif;color:var(--text);background:var(--white)}
.abs{position:absolute}
.heading{font-family:"Oswald","Arial Narrow",sans-serif;font-weight:600;text-transform:uppercase;color:var(--ink);font-size:30px;letter-spacing:-.3px;line-height:1}
.heading .accent{color:var(--blue)}
.underline{display:block;width:74px;height:2px;background:var(--cyan);margin-top:12px}
.btn{position:absolute;display:flex;align-items:center;justify-content:center;background:var(--cyan);color:var(--white);font-weight:700;font-size:16px;text-decoration:none}
.brand{font-family:"Oswald","Arial Narrow",sans-serif;font-weight:600;text-transform:uppercase;letter-spacing:.5px}

/* hero */
.hero{left:0;top:0;width:1200px;height:638px;background:linear-gradient(180deg,#8fa7a2 0%,#a39d91 45%,#7c7a74 100%)}
.hero-photo{position:absolute;inset:0;background:radial-gradient(ellipse 260px 330px at 600px 300px,rgba(150,140,125,.8),rgba(0,0,0,0) 70%)}
.hero-shade{position:absolute;inset:0;background:linear-gradient(180deg,rgba(0,0,0,.15),rgba(0,0,0,.05) 40%,rgba(0,0,0,.35))}
.site-logo{left:160px;top:30px;color:var(--white);font-size:26px;display:flex;align-items:center;gap:10px}
.site-logo .dot{width:12px;height:12px;border-radius:50%;background:var(--white)}
.main-nav{left:537px;top:36px;display:flex;gap:29px}
.main-nav a{color:var(--white);text-decoration:none;font-size:15.5px}
.hero-title{left:150px;top:404px;width:900px;text-align:center;color:var(--white);font-family:"Oswald","Arial Narrow",sans-serif;font-weight:600;font-size:38px;line-height:47px;text-shadow:0 2px 6px rgba(0,0,0,.35)}

/* about */
.about-text{left:160px;top:787px;width:280px;font-size:15.5px;line-height:27px}
.about-text p+p{margin-top:7px}
.photo-main{left:450px;top:727px;width:263px;height:406px;border-radius:8px;background:linear-gradient(180deg,#9cc7c1 0%,#b9bfc0 35%,#9aa0a4 70%,#7d8388 100%)}
.photo-inset{left:576px;top:982px;width:176px;height:189px;background:var(--white);border-radius:8px;box-shadow:0 4px 14px rgba(0,0,0,.25);padding:5px}
.photo-inset .fill{width:100%;height:100%;border-radius:6px;background:linear-gradient(160deg,#3a3d40,#6b6f72 60%,#404346);display:flex;align-items:center;justify-content:center;color:var(--white);font-size:20px}
.why-list{left:774px;top:790px;width:300px;list-style:none}
.why-list li{position:relative;padding-left:32px;font-size:15px;font-weight:700;color:var(--ink);line-height:27px;margin-bottom:12px}
.why-list svg{position:absolute;left:0;top:5px}

/* services */
.services{left:0;top:1260px;width:1200px;height:579px;background:var(--section-grey)}
.service{position:absolute;width:240px}
.service .ico{display:block;height:62px;margin-bottom:18px}
.service h3{font-weight:400;font-size:19px;color:var(--blue-mid);margin-bottom:6px}
.service p{font-size:15.5px;line-height:27px;color:var(--text)}

/* testimonials */
.review{position:absolute;top:2008px;width:262px;height:186px;border:1px solid #dfe3e8;border-radius:4px;padding:22px 20px;background:var(--white)}
.review .stars{font-size:13px;color:var(--star);letter-spacing:1px}
.review .stars span{color:#dcdcdc}
.review .src{position:absolute;right:20px;top:24px;width:14px;height:14px;border-radius:50%;border:3px solid var(--blue-mid)}
.review .when{font-size:12.5px;color:var(--muted);margin-top:6px}
.review .body{font-size:13.5px;line-height:22px;color:var(--text);margin-top:10px}
.review .who{font-size:13.5px;color:var(--muted);margin-top:6px}
.arrow{position:absolute;width:32px;height:32px;border-radius:50%;display:flex;align-items:center;justify-content:center}

/* footer */
.footer{left:0;top:2405px;width:1200px;height:527px;background:var(--footer);color:var(--white)}
.foot-logo{left:0;top:95px;width:1200px;text-align:center;font-size:48px;color:var(--white);line-height:1}
.foot-rule{left:285px;top:200px;width:630px;height:1px;background:rgba(255,255,255,.15)}
.foot-nav{left:254px;top:230px;display:flex;gap:40px;align-items:center}
.foot-nav a{color:var(--white);text-decoration:none;font-size:16.5px}
.social{display:flex;gap:13px;margin-left:-5px}
.social span{width:30px;height:30px;border-radius:50%;background:var(--white)}
.contact-row{font-size:15px;line-height:25px}
</style>
</head>
<body>

<!-- Hero -->
<header class="abs hero">
  <div class="hero-photo" role="img" aria-label="Photo of a young woman in a knit beanie adjusting her earphones inside a laundromat with front-load washers behind her"></div>
  <div class="hero-shade"></div>
  <div class="abs site-logo brand"><span class="dot"></span>Suds Haven</div>
  <nav class="abs main-nav">
    <a href="#">Home</a><a href="#">About Us</a><a href="#">Services</a><a href="#">Locations</a><a href="#">Reviews</a><a href="#">Contact Us</a>
  </nav>
  <h1 class="abs hero-title">We Provide Fast, Friendly &amp; Professional Dry Cleaning And Laundry Service In Midtown Atlanta, USA</h1>
  <a class="btn" href="#" style="left:543px;top:513px;width:113px;height:42px">Visit Us</a>
</header>

<!-- About -->
<section>
  <h2 class="abs heading" style="left:160px;top:722px">About <span class="accent">Suds Haven</span><span class="underline"></span></h2>
  <div class="abs about-text">
    <p>Lorem ipsum dolor sit amet, consectetuer adipiscing elit, sed diam nonummy nibh euismod tincidunt ut laoreet dolore magna aliquam erat volutpat.</p>
    <p>Ut wisi enim ad minim veniam, quis nostrud exerci tation ullamcorper suscipit lobortis nisl ut aliquip ex ea commodo consequat. Duis autem vel eum iriure dolor in hendrerit in vulputate velit esse molestie vel illum dolore.</p>
  </div>
  <a class="btn" href="#" style="left:160px;top:1112px;width:113px;height:41px">Read More</a>

  <div class="abs photo-main" role="img" aria-label="Photo of the laundromat interior with rows of stainless steel washers and potted plants"></div>
  <div class="abs photo-inset"><div class="fill brand" role="img" aria-label="Close-up photo of a washer with the shop name">Suds Haven</div></div>

  <h2 class="abs heading" style="left:774px;top:722px">Why <span class="accent">Choose Us?</span><span class="underline"></span></h2>
  <ul class="abs why-list">
    <li><svg width="20" height="20" viewBox="0 0 20 20"><circle cx="10" cy="10" r="8.5" fill="none" stroke="#0677BA" stroke-width="1.6"/><path d="M5.5 10l3 3 6-7" fill="none" stroke="#0677BA" stroke-width="2"/></svg>In Business over 45 years</li>
    <li><svg width="20" height="20" viewBox="0 0 20 20"><circle cx="10" cy="10" r="8.5" fill="none" stroke="#0677BA" stroke-width="1.6"/><path d="M5.5 10l3 3 6-7" fill="none" stroke="#0677BA" stroke-width="2"/></svg>Voted "BEST COIN LAUNDRY" - Multiple years</li>
    <li><svg width="20" height="20" viewBox="0 0 20 20"><circle cx="10" cy="10" r="8.5" fill="none" stroke="#0677BA" stroke-width="1.6"/><path d="M5.5 10l3 3 6-7" fill="none" stroke="#0677BA" stroke-width="2"/></svg>One of Atlanta's First, Finest, &amp; Friendliest Coin Laundries</li>
    <li><svg width="20" height="20" viewBox="0 0 20 20"><circle cx="10" cy="10" r="8.5" fill="none" stroke="#0677BA" stroke-width="1.6"/><path d="M5.5 10l3 3 6-7" fill="none" stroke="#0677BA" stroke-width="2"/></svg>The best Wash-Dry-Fold in Town</li>
    <li><svg width="20" height="20" viewBox="0 0 20 20"><circle cx="10" cy="10" r="8.5" fill="none" stroke="#0677BA" stroke-width="1.6"/><path d="M5.5 10l3 3 6-7" fill="none" stroke="#0677BA" stroke-width="2"/></svg>Cool - Comfortable - Clean</li>
    <li><svg width="20" height="20" viewBox="0 0 20 20"><circle cx="10" cy="10" r="8.5" fill="none" stroke="#0677BA" stroke-width="1.6"/><path d="M5.5 10l3 3 6-7" fill="none" stroke="#0677BA" stroke-width="2"/></svg>Over 50 Well Maintained Machines</li>
    <li><svg width="20" height="20" viewBox="0 0 20 20"><circle cx="10" cy="10" r="8.5" fill="none" stroke="#0677BA" stroke-width="1.6"/><path d="M5.5 10l3 3 6-7" fill="none" stroke="#0677BA" stroke-width="2"/></svg>Commercial Accounts</li>
  </ul>
  <a class="btn" href="#" style="left:774px;top:1129px;width:113px;height:41px">Contact Us</a>
</section>

<!-- Services -->
<section class="abs services">
  <svg class="abs" style="left:156px;top:110px" width="340" height="340" viewBox="0 0 340 340">
    <circle cx="201" cy="13" r="8" fill="none" stroke="#0054AA" stroke-width="4"/>
    <circle cx="147" cy="43" r="5" fill="none" stroke="#0054AA" stroke-width="2.5"/>
    <circle cx="247" cy="42" r="5" fill="none" stroke="#0054AA" stroke-width="2.5"/>
    <circle cx="167" cy="218" r="162" fill="#0054AA"/>
  </svg>
  <div class="abs" role="img" aria-label="Round photo of two stainless steel front-load washers" style="left:167px;top:165px;width:318px;height:318px;border-radius:50%;background:linear-gradient(135deg,#d9d5cc,#a9aaa8 50%,#6f7375)"></div>

  <h2 class="abs heading" style="left:529px;top:88px">Our <span class="accent">Services</span><span class="underline"></span></h2>

  <div class="service" style="left:529px;top:161px">
    <svg class="ico" width="62" height="62" viewBox="0 0 62 62" fill="none" stroke="#0677BA" stroke-width="2"><rect x="6" y="4" width="50" height="54" rx="3"/><line x1="6" y1="16" x2="56" y2="16"/><circle cx="31" cy="37" r="14"/><circle cx="31" cy="37" r="9"/></svg>
    <h3>Dry Cleaning Drop Off</h3>
    <p>Lorem ipsum dolor sit amet, consectetuer adipiscing elit.</p>
  </div>
  <div class="service" style="left:780px;top:161px">
    <svg class="ico" width="62" height="62" viewBox="0 0 62 62" fill="none" stroke="#0677BA" stroke-width="2"><path d="M31 4v6M8 22l23-12 23 12H8z"/><rect x="4" y="28" width="30" height="30" rx="2"/><circle cx="19" cy="45" r="8"/><path d="M40 58l16-20M40 38l16 20"/></svg>
    <h3>Professional Laundry Services</h3>
    <p>Lorem ipsum dolor sit amet, consectetuer adipiscing elit.</p>
  </div>
  <div class="service" style="left:529px;top:345px">
    <svg class="ico" width="62" height="62" viewBox="0 0 62 62" fill="none" stroke="#0677BA" stroke-width="2"><path d="M31 6a5 5 0 1 1 0 8v4L8 30h46L31 18"/><path d="M12 30v28h38V30"/><path d="M31 30v28"/></svg>
    <h3>Wash Dry Fold</h3>
    <p>Lorem ipsum dolor sit amet, consectetuer adipiscing elit.</p>
  </div>
  <div class="service" style="left:780px;top:345px">
    <svg class="ico" width="62" height="62" viewBox="0 0 62 62" fill="none" stroke="#0677BA" stroke-width="2"><rect x="30" y="26" width="28" height="32" rx="2"/><circle cx="44" cy="44" r="8"/><rect x="4" y="30" width="20" height="28" rx="2"/><path d="M14 30v-8M8 22h12"/></svg>
    <h3>Self Service Laundry</h3>
    <p>Lorem ipsum dolor sit amet, consectetuer adipiscing elit.</p>
  </div>
</section>

<!-- Testimonials -->
<section>
  <h2 class="abs heading" style="left:0;top:1925px;width:1200px;text-align:center">Customer <span class="accent">Testimonials</span><span class="underline" style="margin:12px auto 0"></span></h2>

  <div class="arrow" style="left:116px;top:2085px;border:1.5px solid var(--ink)"><svg width="12" height="10" viewBox="0 0 12 10"><path d="M11 5H2M5 1L1 5l4 4" fill="none" stroke="#222831" stroke-width="1.6"/></svg></div>

  <article class="review" style="left:172px">
    <div class="stars">★★★<span>★★</span></div><i class="src"></i>
    <div class="when">4 Days Ago</div>
    <p class="body">Lorem ipsum dolor sit amet, cons ect etuer adipiscing elit, sed diam nonum my nibh euismod.</p>
    <div class="who">Dana Mercer</div>
  </article>
  <article class="review" style="left:469px">
    <div class="stars">★★★<span>★★</span></div><i class="src"></i>
    <div class="when">2 Weeks Ago</div>
    <p class="body">Lorem ipsum dolor sit amet, cons ect etuer adipiscing elit, sed diam nonum my nibh euismod.</p>
    <div class="who">Owen Castillo</div>
  </article>
  <article class="review" style="left:766px">
    <div class="stars">★★★<span>★★</span></div><i class="src"></i>
    <div class="when">1 Months Ago</div>
    <p class="body">Lorem ipsum dolor sit amet, cons ect etuer adipiscing elit, sed diam nonum my nibh euismod.</p>
    <div class="who">Priya Lang</div>
  </article>

  <div class="arrow" style="left:1051px;top:2085px;border:1.5px solid var(--cyan)"><svg width="12" height="10" viewBox="0 0 12 10"><path d="M1 5h9M7 1l4 4-4 4" fill="none" stroke="#03A2E0" stroke-width="1.6"/></svg></div>

  <div class="abs" style="left:0;top:2220px;width:1200px;display:flex;justify-content:center;align-items:center;gap:8px;font-size:13.5px;color:var(--ink)">
    Rated <b>4.3</b> of 5 based on <b>9818 reviews</b>
    <span style="width:26px;height:26px;border:1px solid #dfe3e8;display:flex;align-items:center;justify-content:center"><i style="width:13px;height:13px;border-radius:50%;border:3px solid var(--blue-mid)"></i></span>
    <b>Online reviews</b>
  </div>
  <a class="btn" href="#" style="left:543px;top:2274px;width:113px;height:41px">View All</a>
</section>

<!-- Footer -->
<footer class="abs footer">
  <div class="abs foot-logo brand">Suds Haven</div>
  <div class="abs foot-rule"></div>
  <nav class="abs foot-nav">
    <a href="#">Home</a><a href="#">About Us</a><a href="#">Services</a><a href="#">Locations</a><a href="#">Reviews</a><a href="#">Contact Us</a>
    <div class="social"><span></span><span></span></div>
  </nav>

  <div class="abs contact-row" style="left:246px;top:305px;width:350px">
    <svg class="abs" style="left:0;top:3px" width="18" height="18" viewBox="0 0 18 18" fill="none" stroke="#fff" stroke-width="1.3"><path d="M9 17s-6-6-6-10a6 6 0 0 1 12 0c0 4-6 10-6 10z"/><circle cx="9" cy="7" r="2"/></svg>
    <p style="padding-left:30px">Birchgate Plaza, 2210 Larkspur Ave NE., # 118, Atlanta, GA 30399</p>
    <svg class="abs" style="left:0;top:61px" width="18" height="18" viewBox="0 0 18 18" fill="none" stroke="#fff" stroke-width="1.3"><path d="M4 1l3 4-2 2a10 10 0 0 0 6 6l2-2 4 3-2 3C8 17 1 10 1 4z"/></svg>
    <p style="padding-left:30px;margin-top:9px">(404) 555-0148</p>
  </div>
  <div class="abs contact-row" style="left:611px;top:305px;width:360px">
    <p style="color:var(--cyan)"><b>Delivery Available*</b> please contact us for details</p>
    <p style="margin-top:7px">Covid 19 hours - open 7 days a week 8 am to 8 pm<br>Last wash begins 6:30 pm</p>
  </div>

  <div class="abs" style="left:160px;top:417px;width:880px;height:1px;background:rgba(255,255,255,.15)"></div>
  <p class="abs" style="left:0;top:464px;width:1200px;text-align:center;font-size:13.5px">Copyright © 2021 <b>Suds Haven Atlanta</b>. All Rights Reserved.</p>
</footer>

</body>
</html>
```